Local Flower Farm Needs Business Card Design

I need business cards designed for a flower farm based in Eudora, Kansas.
Business Info:
We are a local cut flower farm located in Eudora, Kansas, founded by Corinne Haldwick. What started as a passion for agriculture and search for more joy in daily life has blossomed into a small business dedicated to providing the community with beautiful, fresh, and sustainable flowers. We specialize in local, seasonal blooms, ensuring that every petal reflects the care and dedication we pour into our craft. Our mission is to deliver the highest quality flowers directly to our customers through local farmers markets and to florists who share our commitment to sustainability. Join us in celebrating the beauty of nature, one bloom at a time!
Contact Details:
Corinne Haldwick
Owner
Phone 913-555-0147
Facebook: Rosalind Thorpe Gardens
Instagram: @RosalindThorpeGardens
Website: RosalindThorpeGardens.example
Target Market(s)
Wholesale to Florists and Direct to Consumer via Farmers Market
Industry/Entity Type
Florist, Farm
Contact Information for Business Card
Name, Contact Info, Logo
Look and feel
Each slider illustrates characteristics of the customer's brand and the style your logo design should communicate.

```html
<!DOCTYPE html>
<html lang="en">
<head>
<meta charset="utf-8">
<title>Rosalind Thorpe Gardens — Business Card</title>
<link rel="stylesheet" href="https://fonts.googleapis.com/css2?family=Playfair+Display:wght@500&family=Montserrat:wght@400;500&display=swap">
<style>
  :root{
    --ink:#0f262b;
    --ink-soft:#132f35;
    --teal:#2a7f8c;
    --paper:#ffffff;
    --stage:#2f3132;
    --line-light:#cfdadb;
    --sprig:#eef3f3;
  }
  *{margin:0;padding:0;box-sizing:border-box}
  html,body{width:1200px;height:866px;overflow:hidden;background:var(--stage)}
  .stage{position:relative;width:1200px;height:866px}
  .card{position:absolute;top:273px;width:560px;height:320px;overflow:hidden}
  .card--front{left:30px;background:var(--paper)}
  .card--back{left:610px;background:var(--ink)}
  .card__art{position:absolute;inset:0}

  .holder{position:absolute;left:34px;top:26px;color:var(--ink)}
  .holder__name{font-family:"Playfair Display",serif;font-weight:500;font-size:23px;letter-spacing:.09em;text-transform:uppercase;line-height:1}
  .holder__role{font-family:"Montserrat",sans-serif;font-size:13px;margin-top:3px}

  .contacts{position:absolute;left:20px;top:166px;list-style:none;color:var(--paper);font-family:"Montserrat",sans-serif;font-size:13.5px;line-height:23px}
  .contacts li{display:flex;align-items:center;gap:7px;white-space:nowrap}
  .contacts .icon{display:block;width:16px;height:16px;flex:none}

  .brand{position:absolute;display:flex;align-items:center;justify-content:center;text-align:center;border-radius:50%;font-family:"Playfair Display",serif;font-weight:500;text-transform:uppercase;letter-spacing:.14em;line-height:1.5}
  .card--front .brand{left:360px;top:95px;width:160px;height:160px;border:1.5px solid var(--ink);color:var(--ink);font-size:15px}
  .card--back .brand{left:185px;top:65px;width:190px;height:190px;border:1.5px solid var(--line-light);color:var(--paper);font-size:17px}
</style>
</head>
<body>
<main class="stage">

  <section class="card card--front">
    <svg class="card__art" viewBox="0 0 560 320" width="560" height="320">
      <path d="M0,112 C150,72 235,140 310,228 C370,296 420,312 470,320 L0,320 Z" fill="var(--ink)"/>
      <path d="M0,103 C150,63 238,132 314,220 C374,290 424,306 480,316" fill="none" stroke="var(--teal)" stroke-width="3"/>
      <path d="M0,97 C150,57 242,126 318,214 C378,284 428,300 490,312" fill="none" stroke="var(--ink)" stroke-width="1"/>
      <rect x="445" y="272" width="95" height="30" rx="14" fill="var(--sprig)" role="img" aria-label="Line-drawn wildflower sprigs along the wave"/>
    </svg>

    <div class="holder">
      <p class="holder__name">Corinne Haldwick</p>
      <p class="holder__role">Owner</p>
    </div>

    <ul class="contacts">
      <li><svg class="icon" viewBox="0 0 16 16"><circle cx="8" cy="8" r="7" fill="none" stroke="#fff"/><path d="M5.5 4.5l1.5 1.8-.8 1c.6 1.1 1.3 1.8 2.4 2.4l1-.8 1.8 1.5-.9 1.1c-2.8-.4-5.2-2.8-5.6-5.6z" fill="#fff"/></svg>913-555-0147</li>
      <li><svg class="icon" viewBox="0 0 16 16"><circle cx="8" cy="8" r="7" fill="none" stroke="#fff"/></svg>Rosalind Thorpe Gardens</li>
      <li><svg class="icon" viewBox="0 0 16 16"><circle cx="8" cy="8" r="7" fill="none" stroke="#fff"/></svg>@RosalindThorpeGardens</li>
      <li><svg class="icon" viewBox="0 0 16 16"><circle cx="8" cy="8" r="7" fill="none" stroke="#fff"/></svg>RosalindThorpeGardens.example</li>
    </ul>

    <div class="brand">Rosalind<br>Thorpe<br>Gardens</div>
  </section>

  <section class="card card--back">
    <svg class="card__art" viewBox="0 0 560 320" width="560" height="320">
      <rect x="410" y="60" width="130" height="240" rx="40" fill="var(--ink-soft)" role="img" aria-label="Faint botanical stems drawn as a background texture"/>
    </svg>
    <div class="brand">Rosalind<br>Thorpe<br>Gardens</div>
  </section>

</main>
</body>
</html>
```